we can communicate on this, but i want to follow the approach we took on Pellew|Marsh & Quinlan but i feel the card front needs the black background and the platinum and gold logo. The back? I am open. we can use the same info from PM&Q. Velmont Arc is an enhanced equity investment fund - basically a very exclusive boutique hedge fund that uses only stock options. very advanced things. hope you are interested

Contact Information for Business Card

Dr. Lewis T. Brennick, CFA
Scientifique de fusée financière
701.555.0143
LTBquant47@mailvantor.com

4718 Willow Creek Bend W.
West Fargo, ND 58078

No web site

Colors

Designer to choose colors to be used in the design.

Requirements
Nice to have
• I tend to prefer the most visible applications of the logo to include logo and name, the logo version with a black background and the gold and platinum components separated by the black. I see this working well for a single side (logo and name - this is card front to me).
• I am fairly open to other treatments on the reverse side with the data. To me, it makes sense to have a different color rendition of the logo on the reverse and it may be a muted black tone on tone or an oversized portion that would have spot UV. Or, the reverse may play with colors and layout
Should not have
• Other colors = no no
• Decorative font

```html
<!DOCTYPE html>
<html lang="en">
<head>
<meta charset="utf-8">
<title>Velmont Arc – Business Card</title>
<link href="https://fonts.googleapis.com/css2?family=Lato:wght@400;700;900&display=swap" rel="stylesheet">
<style>
  :root {
    --stage: #55595b;
    --card-black: #121213;
    --card-white: #ffffff;
    --gold: #b38a2e;
    --ink: #161616;
    --grey-text: #4a4a4a;
    --white: #ffffff;
  }
  * { box-sizing: border-box; margin: 0; padding: 0; }
  html, body {
    width: 1200px; height: 780px; overflow: hidden;
    background: var(--stage);
    font-family: "Lato", Arial, sans-serif;
  }
  .canvas { position: relative; width: 1200px; height: 780px; }

  .card {
    position: absolute;
    width: 560px; height: 320px;
    box-shadow: 0 10px 24px rgba(0,0,0,0.35);
  }

  /* Front */
  .card-front {
    left: 70px; top: 60px;
    background: var(--card-black);
    display: flex; align-items: center; justify-content: center;
  }
  .brand-front { display: flex; align-items: center; gap: 18px; }
  .brand-front .brand-dot {
    width: 62px; height: 62px; border-radius: 50%;
    background: var(--gold);
  }
  .brand-front .brand-name {
    font-weight: 900; font-size: 44px; letter-spacing: 1px;
    color: var(--white); text-transform: uppercase;
  }

  /* Back */
  .card-back {
    left: 570px; top: 400px;
    background: var(--card-white);
  }
  .brand-back {
    position: absolute; right: 34px; top: 40px;
    display: flex; align-items: center; gap: 10px;
  }
  .brand-back .brand-dot {
    width: 38px; height: 38px; border-radius: 50%;
    background: var(--gold);
  }
  .brand-back .brand-name {
    font-weight: 900; font-size: 26px; letter-spacing: 0.5px;
    color: var(--ink); text-transform: uppercase;
  }

  .holder { position: absolute; left: 36px; top: 172px; }
  .holder-name { font-weight: 700; font-size: 24px; line-height: 1.2; color: var(--gold); }
  .holder-title { font-weight: 700; font-size: 14px; color: var(--grey-text); margin-top: 2px; }

  .rule {
    position: absolute; left: 36px; right: 34px; top: 230px;
    height: 1.5px; background: var(--gold);
  }

  .contact { position: absolute; left: 36px; top: 246px; list-style: none; }
  .contact li {
    display: flex; align-items: center; gap: 12px;
    font-size: 14px; color: var(--grey-text); height: 26px;
    white-space: nowrap;
  }
  .contact svg { width: 16px; height: 16px; flex: none; }
  .icon-phone { fill: var(--gold); }
  .icon-mail { fill: none; stroke: var(--gold); stroke-width: 2; }

  .address {
    position: absolute; right: 34px; top: 246px;
    text-align: right; font-style: normal;
    font-weight: 700; font-size: 13px; line-height: 26px; color: var(--grey-text);
    white-space: nowrap;
  }
</style>
</head>
<body>
<main class="canvas">

  <section class="card card-front" aria-label="Card front">
    <div class="brand-front">
      <span class="brand-dot"></span>
      <span class="brand-name">Velmont Arc</span>
    </div>
  </section>

  <section class="card card-back" aria-label="Card back">
    <div class="brand-back">
      <span class="brand-dot"></span>
      <span class="brand-name">Velmont Arc</span>
    </div>

    <div class="holder">
      <p class="holder-name">Dr. Lewis T. Brennick, CFA</p>
      <p class="holder-title">Scientifique des Fusées Financières</p>
    </div>

    <div class="rule"></div>

    <ul class="contact">
      <li>
        <svg class="icon-phone" viewBox="0 0 24 24" aria-hidden="true"><path d="M6.6 10.8a15.1 15.1 0 0 0 6.6 6.6l2.2-2.2a1 1 0 0 1 1-.25 11.4 11.4 0 0 0 3.6.57 1 1 0 0 1 1 1V20a1 1 0 0 1-1 1A17 17 0 0 1 3 4a1 1 0 0 1 1-1h3.5a1 1 0 0 1 1 1c0 1.25.2 2.45.57 3.57a1 1 0 0 1-.25 1z"/></svg>
        701.555.0143
      </li>
      <li>
        <svg class="icon-mail" viewBox="0 0 24 24" aria-hidden="true"><path d="M2 5h20v14H2z M2 5l10 8 10-8"/></svg>
        LTBquant47@mailvantor.com
      </li>
    </ul>

    <address class="address">
      4718 Willow Creek Bend W.<br>
      West Fargo, ND 58078
    </address>
  </section>

</main>
</body>
</html>
```